Business Card - Tidal Lanes

Need Business Card design for company named Tidal Lanes. Software development focused mainly on Brindle Orvix & Zelt Apps. I've attached our logo with both a black and white background. Please add trademark symbol to logo when using.

```html
<!DOCTYPE html>
<html lang="en">
<head>
<meta charset="utf-8">
<title>Tidal Lanes – Business Card</title>
<link rel="stylesheet" href="https://fonts.googleapis.com/css2?family=Ubuntu:wght@400;500;700&display=swap">
<style>
  :root {
    --backdrop: #e9e4dc;
    --card-dark: #141414;
    --card-mid: #262626;
    --brand-red: #d71d1d;
    --brand-amber: #f7b21a;
    --brand-orange: #f07a1e;
    --text-light: #ffffff;
    --text-soft: #d9d9d9;
  }
  * { box-sizing: border-box; margin: 0; padding: 0; }
  html, body {
    width: 1200px; height: 720px; overflow: hidden;
    background: var(--backdrop);
    font-family: "Ubuntu", sans-serif;
  }
  .sheet { position: relative; width: 1200px; height: 720px; }
  .card {
    position: absolute; top: 205px;
    width: 540px; height: 309px;
    border-radius: 4px;
    overflow: hidden;
    background:
      repeating-linear-gradient(90deg, rgba(255,255,255,0.025) 0 1px, transparent 1px 3px),
      radial-gradient(ellipse at 50% 30%, var(--card-mid), var(--card-dark) 75%);
    box-shadow: 0 6px 18px rgba(0,0,0,0.25);
    color: var(--text-light);
  }
  .card--front { left: 40px; }
  .card--back { left: 620px; }

  .wordmark {
    position: absolute; left: 0; right: 0;
    display: flex; align-items: center; justify-content: center; gap: 12px;
  }
  .wordmark__dot { border-radius: 50%; background: var(--brand-orange); flex: none; }
  .wordmark__name {
    position: relative;
    font-weight: 700; color: var(--text-light); letter-spacing: -0.5px;
    line-height: 1;
  }
  .wordmark__tm {
    position: absolute; top: -0.15em; left: 100%; margin-left: 3px;
    font-size: 0.3em; font-weight: 700; letter-spacing: 0;
    color: var(--text-light);
  }
  .card--front .wordmark { top: 64px; }
  .card--front .wordmark__dot { width: 34px; height: 34px; }
  .card--front .wordmark__name { font-size: 32px; }

  .name-band {
    position: absolute; left: 0; right: 0; top: 140px; height: 40px;
    background: var(--brand-red);
    border-top: 2px solid var(--brand-amber);
    border-bottom: 2px solid var(--brand-amber);
    box-shadow: 0 -5px 0 -3px var(--card-dark), 0 -6px 0 -3px var(--brand-amber),
                0 5px 0 -3px var(--card-dark), 0 6px 0 -3px var(--brand-amber);
    display: flex; align-items: center; justify-content: center;
    font-size: 19px;
  }
  .name-band__name { font-weight: 700; }
  .name-band__title { font-weight: 400; margin-left: 6px; }

  .contact {
    position: absolute; top: 206px; left: 0; right: 0;
    display: flex; justify-content: center; align-items: stretch; gap: 24px;
    font-size: 15px; line-height: 26px; color: var(--text-soft);
  }
  .contact__address { font-style: normal; }
  .contact__divider { width: 1px; background: #777; }
  .contact__phones { list-style: none; }
  .contact__phones li { display: flex; align-items: center; gap: 9px; }
  .contact__icon { width: 14px; height: 14px; }

  .card--back .wordmark { top: 114px; }
  .card--back .wordmark__dot { width: 44px; height: 44px; }
  .card--back .wordmark__name { font-size: 44px; }
  .web {
    position: absolute; left: 0; right: 0; top: 214px;
    text-align: center; font-size: 17px; letter-spacing: 3px; color: var(--text-soft);
  }
</style>
</head>
<body>
<main class="sheet">
  <section class="card card--front" aria-label="Card front">
    <div class="wordmark">
      <span class="wordmark__dot"></span>
      <span class="wordmark__name">Tidal Lanes<span class="wordmark__tm">™</span></span>
    </div>
    <div class="name-band">
      <span class="name-band__name">Your Name,</span>
      <span class="name-band__title">Title</span>
    </div>
    <div class="contact">
      <address class="contact__address">4120 Harbor Row<br>Pelican, FL 33500</address>
      <span class="contact__divider"></span>
      <ul class="contact__phones">
        <li>
          <svg class="contact__icon" viewBox="0 0 14 14" aria-hidden="true">
            <rect x="3" y="0.5" width="8" height="13" rx="1.5" fill="var(--brand-amber)"/>
            <rect x="4.5" y="2" width="5" height="7" fill="var(--card-dark)"/>
          </svg>
          813-555-0190
        </li>
        <li>
          <svg class="contact__icon" viewBox="0 0 14 14" aria-hidden="true">
            <path d="M1 5 Q7 1 13 5 L11 7 L9 5.5 L5 5.5 L3 7 Z" fill="var(--brand-amber)"/>
            <rect x="2" y="8" width="10" height="5" rx="1" fill="var(--brand-amber)"/>
          </svg>
          813-555-0127
        </li>
      </ul>
    </div>
  </section>

  <section class="card card--back" aria-label="Card back">
    <div class="wordmark">
      <span class="wordmark__dot"></span>
      <span class="wordmark__name">Tidal Lanes<span class="wordmark__tm">™</span></span>
    </div>
    <p class="web">www.tidallanes.com</p>
  </section>
</main>
</body>
</html>
```